Business Card - high end, modern health care

Hey designers!

We need a double sided business card for the boutique, cutting edge physical therapy rehabilitation centre in Sydney's Northern Beaches.

With the most qualified physios in the area The Harbourview Motion Clinic does what other physiotherapy practices do not, we take our time with our patients giving them longer appointments, better physios and therefor faster results!

We guarantee that the service people receive at THMC will be unparalleled.

Hence we need a business card to reflect our modern, boutique, high end service. The final design needs to reflect that we are in a class of our own yet with the feel of beachside retreat.

Below I have attached our logo in both blue on white and white on blue. The exact colour is;
and the font that we have used in our logo is Tex Gyre Aventador.

I like the idea of the blue as the main colour as it is more eye catching and our signage onto the main road will be in this blue and in the interest of consistency across marketing the blue needs to be a part of the design. However I would appreciate a few designs onto a wooden background as this is a visual theme within the fitout of the practice.

The design needs to be of standard size (91x55mm).

Target Market(s)

We target people who have an end outcome in mind and those who have had poor experiences with other providers and ensure that everyone gets the care that they deserve with a premium service that is tailored to the individuals circumstances. As a premium service, the target market is highly educated, business and tech savvy with the additional target market of elderly people who have self funded their retirement and see value in paying for the best ongoing rehabilitation to maintain independence.

Industry/Entity Type

Physical Therapy

Contact Information for Business Card

Name, designation( Titled Musculoskeletal Physiotherapist... there will also be those in the company that have multiple designations ie 5 or 6 words long), phone number, email, facebook, instagram, address

Font styles to use
Sans Serif

Colors

Designer to choose colors to be used in the design.

Requirements
Must have
• Front - The logo as large as possible, blue or wooden theme, and all of the important details.
• Back - A blank space/lines on which to write appointment times (no "Appointment, date, time" etc.)
Nice to have
• facebook url
• logos for facebook and instagram
• Mini logos for the phone and email?

```html
<!DOCTYPE html>
<html lang="en">
<head>
<meta charset="utf-8">
<title>The Harbourview Motion Clinic – Business Card</title>
<link rel="stylesheet" href="https://fonts.googleapis.com/css2?family=Raleway:wght@400;500;700&display=swap">
<style>
  :root {
    --backdrop: #55537a;
    --brand-blue: #0d57a5;
    --brand-blue-soft: #2f6db1;
    --paper: #ffffff;
    --ink: #1c1c1c;
    --ink-muted: #333333;
    --rule: #3a3a3a;
    --dash: #b8b8b8;
  }
  * { margin: 0; padding: 0; box-sizing: border-box; }
  html, body {
    width: 1200px; height: 1000px; overflow: hidden;
    background: var(--backdrop);
    font-family: "Raleway", sans-serif;
  }
  .canvas { position: relative; width: 1200px; height: 1000px; }

  .card { position: absolute; width: 658px; height: 375px; overflow: hidden; }

  /* Front */
  .card-front { left: 136px; top: 78px; background: var(--brand-blue); }
  .front-backdrop-circle {
    position: absolute; left: 283px; top: 19px;
    width: 336px; height: 336px; border-radius: 50%;
    background: var(--brand-blue-soft); opacity: 0.55;
  }
  .brand-lockup {
    position: absolute; left: 47px; top: 159px;
    display: flex; align-items: center; gap: 10px;
    color: var(--paper);
  }
  .brand-dot { width: 56px; height: 56px; border-radius: 50%; background: var(--paper); flex: none; }
  .brand-name { font-weight: 700; line-height: 1; text-transform: uppercase; }
  .brand-name .line-one { display: block; font-size: 27px; letter-spacing: 0.5px; }
  .brand-name .line-two { display: block; font-size: 19px; letter-spacing: 5px; margin-top: 5px; }

  /* Back */
  .card-back { left: 437px; top: 548px; background: var(--paper); color: var(--ink); }
  .person-name { position: absolute; left: 48px; top: 72px; font-size: 25px; font-weight: 500; }
  .person-name .accent { color: var(--brand-blue); }
  .person-title { position: absolute; left: 48px; top: 109px; font-size: 14px; font-weight: 500; color: var(--ink-muted); }
  .rule { position: absolute; left: 48px; width: 369px; height: 1px; background: var(--rule); }
  .rule-top { top: 150px; }
  .rule-bottom { top: 247px; }
  .contact-list { position: absolute; left: 47px; top: 175px; list-style: none; }
  .contact-list li { display: flex; align-items: center; gap: 16px; height: 31px; font-size: 17px; font-weight: 500; }
  .contact-list svg { width: 23px; height: 23px; flex: none; }
  .social-list { position: absolute; left: 47px; top: 268px; display: flex; gap: 50px; list-style: none; }
  .social-list li { display: flex; align-items: center; gap: 8px; font-size: 15px; font-weight: 500; color: var(--ink-muted); }
  .social-dot { width: 22px; height: 22px; border-radius: 50%; background: var(--brand-blue); }
  .appointment-line { position: absolute; left: 41px; right: 39px; top: 339px; border-top: 1.5px dashed var(--dash); }
  .back-mark { position: absolute; left: 458px; top: 115px; width: 146px; height: 146px; border-radius: 50%; background: var(--brand-blue); }
</style>
</head>
<body>
<main class="canvas">
  <section class="card card-front" aria-label="Card front">
    <div class="front-backdrop-circle"></div>
    <div class="brand-lockup">
      <span class="brand-dot"></span>
      <span class="brand-name">
        <span class="line-one">The Harbourview</span>
        <span class="line-two">Motion Clinic</span>
      </span>
    </div>
  </section>

  <section class="card card-back" aria-label="Card back">
    <h1 class="person-name">Name of <span class="accent">Person</span></h1>
    <p class="person-title">Designation</p>
    <div class="rule rule-top"></div>
    <ul class="contact-list">
      <li>
        <svg viewBox="0 0 24 24" aria-hidden="true">
          <circle cx="12" cy="12" r="10.5" fill="none" stroke="#111" stroke-width="1.6"/>
          <path d="M8.6 6.8l1.8-.4 1.1 2.6-1.2 1c.6 1.4 1.6 2.5 3 3.1l1-1.2 2.6 1.1-.4 1.8c-.2.6-.8 1-1.4.9-3.9-.5-6.9-3.5-7.4-7.4-.1-.6.3-1.2.9-1.5z" fill="#111"/>
        </svg>
        <span>555.018.4128</span>
      </li>
      <li>
        <svg viewBox="0 0 24 24" aria-hidden="true">
          <rect x="1" y="5" width="22" height="14" fill="#111"/>
          <path d="M1.5 5.5L12 13.5 22.5 5.5" fill="none" stroke="#fff" stroke-width="1.4"/>
          <path d="M1.5 18.5l8-6.5M22.5 18.5l-8-6.5" fill="none" stroke="#fff" stroke-width="1.2"/>
        </svg>
        <span>hello@harbourviewmotion.com</span>
      </li>
    </ul>
    <div class="rule rule-bottom"></div>
    <ul class="social-list">
      <li><span class="social-dot"></span><span>facebook/name</span></li>
      <li><span class="social-dot"></span><span>instagram_name</span></li>
    </ul>
    <div class="appointment-line"></div>
    <div class="back-mark"></div>
  </section>
</main>
</body>
</html>
```